Quillbrook IT company focused on 3 areas of IT

Looking for something similar to attached cards. Logo for quillbrook also attached.. Looking for something clean as far as colors (surprise me).. Quill stands for 3 primary areas, web design, consulting and network infrastructure design. Please email me if you have any questions. Looking forward to seeing how creative and professional this card will look. Thank you,

Target Market(s)

Small business/consumers looking for It services

Industry/Entity Type

It Service

Contact Information for Business Card

Dorin Vasek
Principal Consultant

202-555-0173

www.quillbrook-example.com
dvasek@quillbrook-example.com

27416 Copper Lantern Way,
Germantown, MD 20999

Colors

Designer to choose colors to be used in the design.

Requirements
Must have
• attached Logo design. Feel free to play with the colors.. If you have a better idea for a card, please fee free to send me. Looking for something clean/modern. Should have tech feel, not cheesy.
Nice to have
• Surprise me :-)..

```html
<!DOCTYPE html>
<html lang="en">
<head>
<meta charset="utf-8">
<title>Quillbrook Business Card</title>
<link href="https://fonts.googleapis.com/css2?family=Work+Sans:wght@400;500;600&display=swap" rel="stylesheet">
<style>
  :root {
    --backdrop: #1c1c1d;
    --card: #121213;
    --card-edge: #2a2a2c;
    --silver: #d9d9db;
    --silver-soft: #bdbdc0;
    --ink-deep: #2b2b2d;
    --divider: #4a4a4d;
  }
  * { margin: 0; padding: 0; box-sizing: border-box; }
  html, body {
    width: 1200px;
    height: 900px;
    overflow: hidden;
    background: var(--backdrop);
    font-family: "Work Sans", Arial, sans-serif;
  }
  .canvas {
    position: relative;
    width: 1200px;
    height: 900px;
  }
  .card {
    position: absolute;
    left: 250px;
    width: 700px;
    height: 400px;
    background: var(--card);
    border: 1px solid var(--card-edge);
    border-radius: 3px;
  }
  .card--front { top: 40px; }
  .card--back { top: 460px; }

  .front-brand {
    position: absolute;
    inset: 0;
    display: flex;
    align-items: center;
    justify-content: center;
    gap: 18px;
  }
  .brand-square {
    width: 26px;
    height: 26px;
    background: var(--silver);
  }
  .brand-name {
    font-weight: 600;
    font-size: 58px;
    letter-spacing: 1px;
    color: var(--silver);
  }

  .back-brand {
    position: absolute;
    left: 0;
    top: 0;
    width: 290px;
    height: 100%;
    display: flex;
    align-items: center;
    justify-content: center;
  }
  .back-brand .brand-name {
    font-size: 40px;
    color: var(--ink-deep);
  }
  .divider {
    position: absolute;
    left: 300px;
    top: 110px;
    width: 1px;
    height: 180px;
    background: var(--divider);
  }
  .contact {
    position: absolute;
    left: 345px;
    top: 100px;
    color: var(--silver);
  }
  .contact__name {
    font-size: 30px;
    font-weight: 500;
    letter-spacing: 2px;
    text-transform: uppercase;
  }
  .contact__title {
    font-size: 15px;
    letter-spacing: 1px;
    color: var(--silver-soft);
    margin-bottom: 12px;
  }
  .contact__address {
    font-size: 16px;
    line-height: 1.5;
    letter-spacing: 0.8px;
    margin-bottom: 10px;
  }
  .contact__list { list-style: none; }
  .contact__item {
    display: flex;
    align-items: center;
    gap: 10px;
    font-size: 16px;
    line-height: 1.6;
    letter-spacing: 0.8px;
  }
  .contact__icon {
    width: 12px;
    height: 12px;
    flex: none;
  }
</style>
</head>
<body>
<main class="canvas">
  <section class="card card--front">
    <div class="front-brand">
      <span class="brand-square"></span>
      <span class="brand-name">Quillbrook</span>
    </div>
  </section>

  <section class="card card--back">
    <div class="back-brand">
      <span class="brand-name">Quillbrook</span>
    </div>
    <div class="divider"></div>
    <div class="contact">
      <h1 class="contact__name">Dorin Vasek</h1>
      <p class="contact__title">Principal Consultant</p>
      <p class="contact__address">27416 Copper Lantern Way,<br>Germantown, MD 20999</p>
      <ul class="contact__list">
        <li class="contact__item">
          <svg class="contact__icon" viewBox="0 0 12 12"><path d="M2.5 1 L4.5 1 L5.2 3.5 L4 4.5 Q5 7 7.5 8 L8.5 6.8 L11 7.5 L11 9.5 Q10.5 11 9 11 Q1 10 1 2.5 Q1 1 2.5 1 Z" fill="#bdbdc0"/></svg>
          202-555-0173
        </li>
        <li class="contact__item">
          <svg class="contact__icon" viewBox="0 0 12 12"><rect x="0.8" y="2.3" width="10.4" height="7.4" fill="none" stroke="#bdbdc0" stroke-width="1.2"/><path d="M1 2.6 L6 6.6 L11 2.6" fill="none" stroke="#bdbdc0" stroke-width="1.2"/></svg>
          dvasek@quillbrook-example.com
        </li>
        <li class="contact__item">
          <svg class="contact__icon" viewBox="0 0 12 12"><circle cx="6" cy="6" r="5" fill="none" stroke="#bdbdc0" stroke-width="1.1"/><ellipse cx="6" cy="6" rx="2.2" ry="5" fill="none" stroke="#bdbdc0" stroke-width="1"/><path d="M1 6 H11" stroke="#bdbdc0" stroke-width="1"/></svg>
          www.quillbrook-example.com
        </li>
      </ul>
    </div>
  </section>
</main>
</body>
</html>
```